Business Card Design needed for start up company Halvora

In need of a new business card designed for a start up company based in Sydney, Halvora is a new start up innovative Company, our mission it to make property accessible for everyday Australian and to become the leading Real Estate platform in Australia. We want it to be fresh and clean.

Industry/Entity Type

Financial

Contact Information for Business Card

Section for Name
Section for Title

HALVORA - The Strength of Pooling
Mobile:
Direct:

Font styles to use
Sans Serif

Colors
33a6d7
0692cd
0255a3
ffffff

Requirements
Must have
• Logo, all business card details

```html
<!DOCTYPE html>
<html lang="en">
<head>
<meta charset="utf-8">
<title>Halvora Business Card</title>
<link href="https://fonts.googleapis.com/css2?family=Jost:wght@400;500;600;700&display=swap" rel="stylesheet">
<style>
  :root {
    --navy: #21417a;
    --sky: #2a9fdb;
    --paper: #f2f2f2;
    --ink: #4a4a4a;
    --white: #ffffff;
    --backdrop: #2b2b2b;
    --rule: #b9b9b9;
  }
  * { margin: 0; padding: 0; box-sizing: border-box; }
  html, body { width: 1200px; height: 960px; overflow: hidden; }
  body {
    background: var(--backdrop);
    font-family: "Jost", "Helvetica Neue", Arial, sans-serif;
    position: relative;
  }
  .card {
    position: absolute;
    width: 600px;
    height: 342px;
    border-radius: 22px;
    overflow: hidden;
  }
  .card--front { left: 302px; top: 124px; background: var(--paper); }
  .card--back { left: 299px; top: 493px; background: var(--navy); }

  .brand { position: absolute; display: flex; align-items: center; }
  .brand__dot { border-radius: 50%; background: var(--sky); flex: none; }
  .brand__name { font-weight: 700; letter-spacing: 0.3px; line-height: 1; white-space: nowrap; }

  .card--front .brand { left: 0; width: 327px; top: 140px; justify-content: center; padding-left: 40px; }
  .card--front .brand__dot { width: 64px; height: 64px; margin-right: 8px; }
  .card--front .brand__name { font-size: 33px; color: var(--navy); }

  .divider {
    position: absolute;
    left: 327px; top: 82px;
    width: 1px; height: 180px;
    background: linear-gradient(to bottom, transparent, var(--rule) 20%, var(--rule) 80%, transparent);
  }

  .details { position: absolute; left: 356px; top: 84px; color: var(--ink); }
  .details__name { font-size: 23px; font-weight: 600; color: var(--navy); line-height: 1.05; letter-spacing: 0.3px; }
  .details__title { font-size: 16px; color: var(--sky); line-height: 1.2; margin-bottom: 12px; }
  .details__address { font-size: 15px; line-height: 19px; margin-bottom: 8px; }
  .contact { list-style: none; font-size: 15px; }
  .contact li { display: flex; align-items: center; height: 19.5px; }
  .contact svg { width: 13px; height: 13px; margin-right: 9px; fill: var(--navy); flex: none; }

  .card--back .brand { left: 0; right: 0; top: 116px; justify-content: center; }
  .card--back .brand__dot { width: 106px; height: 106px; margin-right: 12px; }
  .card--back .brand__name { font-size: 50px; color: var(--white); }

  .tagline {
    position: absolute; left: 0; right: 0; top: 284px;
    text-align: center; color: var(--white); font-size: 17px;
  }
</style>
</head>
<body>
  <section class="card card--front">
    <div class="brand">
      <span class="brand__dot"></span>
      <span class="brand__name">HALVORA</span>
    </div>
    <div class="divider"></div>
    <div class="details">
      <p class="details__name">MARCUS REED</p>
      <p class="details__title">CEO/FOUNDER</p>
      <p class="details__address">2140 Larkspur Road<br>Fairview, Oregon 48213</p>
      <ul class="contact">
        <li>
          <svg viewBox="0 0 16 16" aria-hidden="true"><path d="M3.6 1.2l2.2 2.6c.3.4.3.9 0 1.2L4.7 6.3c.9 2 2.5 3.6 4.6 4.6l1.3-1.1c.4-.3.9-.3 1.2 0l2.6 2.2c.4.3.4.9.1 1.3l-1.2 1.3c-.5.5-1.2.7-1.9.5C6.6 13.8 2.2 9.4 1 4.6.8 3.9 1 3.2 1.5 2.7L2.3 1.1c.4-.3 1-.3 1.3.1z"/></svg>
          614 275 9083
        </li>
        <li>
          <svg viewBox="0 0 16 16" aria-hidden="true"><path d="M4.5 0h7c.8 0 1.5.7 1.5 1.5v13c0 .8-.7 1.5-1.5 1.5h-7C3.7 16 3 15.3 3 14.5v-13C3 .7 3.7 0 4.5 0zM4.8 2v10.5h6.4V2H4.8zM8 13.3a.9.9 0 100 1.8.9.9 0 000-1.8z"/></svg>
          752 309 4186
        </li>
        <li>
          <svg viewBox="0 0 16 16" aria-hidden="true"><path d="M1 3.5h14v.8L8 9 1 4.3v-.8zM1 5.6l7 4.7 7-4.7v7H1v-7z"/></svg>
          marcus@halvora.com
        </li>
        <li>
          <svg viewBox="0 0 16 16" aria-hidden="true"><path d="M8 .8a7.2 7.2 0 100 14.4A7.2 7.2 0 008 .8zm-1 2.4c.7.4.5 1.3 1.3 1.6.9.3 1.6-.4 2.2.3.5.6-.3 1.4-.9 1.7-.8.4-1.8.1-2.2.9-.4.8.6 1.6.2 2.5-.3.7-1.2.6-1.5 1.4-.2.6.2 1.4-.2 1.8C3.8 12.6 2.4 10.5 2.4 8c0-2.5 1.8-4.6 4.6-4.8zm5.2 3.2c.8.3 1.2 1 1.2 1.9 0 1.6-.8 3.1-2 4-.5-.5-.3-1.3 0-1.900.4-.7.3-1.4-.1-2-.3-.5 0-1.6.9-2z"/></svg>
          www.halvora.com
        </li>
      </ul>
    </div>
  </section>

  <section class="card card--back">
    <div class="brand">
      <span class="brand__dot"></span>
      <span class="brand__name">HALVORA</span>
    </div>
    <p class="tagline">The Strength of Pooling</p>
  </section>
</body>
</html>
```